We are a new company with 2 divisions a medical research and medical product sales. We need a company logo and Business Cards. The design files need to be provided to us in Adobe Photoshop CS 5.1.

Target Market(s)

Medical Community

Industry/Entity Type

Medical

Contact Information for Business Card

Company Name - Harrowgate Lifesciences LLC
Company Address 4127 Larkspur Ave Suite 7, Gainesville Fl 32614

Requirements
Must have
• The design files need to be provided to us in Adobe Photoshop CS 5.1.

```html
<!DOCTYPE html>
<html lang="en">
<head>
<meta charset="utf-8">
<title>Harrowgate Lifesciences LLC – Business Card</title>
<link href="https://fonts.googleapis.com/css2?family=Lato:wght@400;700&display=swap" rel="stylesheet">
<style>
  :root {
    --page: #2b2b2b;
    --card-blue: #3387c9;
    --ink-white: #ffffff;
    --ink-navy: #163656;
    --rule: #a8cdec;
  }
  * { margin: 0; padding: 0; box-sizing: border-box; }
  html, body {
    width: 1200px; height: 900px; overflow: hidden;
    background: var(--page);
    font-family: "Lato", sans-serif;
  }
  .card {
    position: absolute;
    left: 145px; top: 191px;
    width: 910px; height: 518px;
    background: var(--card-blue);
    border-radius: 25px;
    box-shadow: 0 10px 30px rgba(0,0,0,0.45);
  }
  .brand {
    position: absolute;
    left: 70px; top: 100px;
    width: 320px;
    text-align: center;
  }
  .brand-dot {
    display: block;
    width: 64px; height: 64px;
    margin: 0 auto 40px;
    border-radius: 50%;
    border: 4px solid var(--ink-navy);
  }
  .brand-name {
    color: var(--ink-white);
    font-weight: 700;
    font-size: 30px;
    line-height: 1.15;
    letter-spacing: 0.5px;
  }
  .person {
    position: absolute;
    right: 88px; top: 186px;
    text-align: right;
  }
  .person-name {
    color: var(--ink-white);
    font-weight: 700;
    font-size: 24px;
    line-height: 1.2;
  }
  .person-title {
    color: var(--ink-navy);
    font-size: 19px;
    line-height: 1.3;
  }
  .divider {
    position: absolute;
    left: 399px; right: 88px; top: 275px;
    height: 1px;
    background: var(--rule);
  }
  .contact {
    position: absolute;
    right: 88px; top: 307px;
    text-align: right;
    color: var(--ink-white);
    font-size: 17.5px;
    line-height: 23px;
  }
  .address { margin-bottom: 19px; }
  .contact-line {
    display: flex; justify-content: flex-end; align-items: center;
    gap: 10px; height: 29px;
  }
  .icon { width: 16px; height: 16px; fill: none; stroke: var(--ink-white); stroke-width: 1.8; }
  .icon.solid { fill: var(--ink-white); stroke: none; }
</style>
</head>
<body>
  <section class="card">
    <div class="brand">
      <span class="brand-dot"></span>
      <p class="brand-name">Harrowgate<br>Lifesciences LLC</p>
    </div>

    <div class="person">
      <p class="person-name">Name of the Person</p>
      <p class="person-title">Managing Director</p>
    </div>

    <div class="divider"></div>

    <div class="contact">
      <p class="address">4127 Larkspur Ave Suite 7,<br>Gainesville Fl 32614</p>
      <p class="contact-line">044 1290 48617
        <svg class="icon solid" viewBox="0 0 16 16" aria-hidden="true"><path d="M2 6c0-2 3-3 6-3s6 1 6 3v1h-3V6H5v1H2z"/><path d="M4 8h8l1 5H3z"/></svg>
      </p>
      <p class="contact-line">info@harrowgatelifesciences.com
        <svg class="icon solid" viewBox="0 0 16 16" aria-hidden="true"><path d="M1 3h14v10H1z"/><path d="M1 3l7 6 7-6" stroke="#3387c9" stroke-width="1.4" fill="none"/></svg>
      </p>
      <p class="contact-line">www.harrowgatelifesciences.com
        <svg class="icon" viewBox="0 0 16 16" aria-hidden="true"><path d="M7 9l-2.5 2.5a2 2 0 0 1-3-3L4 6M9 7l2.5-2.5a2 2 0 0 1 3 3L12 10M6 10l4-4"/></svg>
      </p>
    </div>
  </section>
</body>
</html>
```